High Tech Real Estate Startup needs a business card

We are developing an innovative real estate marketing product based around advanced search and virtual reality.

We talk to people, we need business cards.

Target Market(s)

The target market is technology professionals and realtors.

Contact Information for Business Card

The information to be included will include

Name
Title
Phone Number
E-mail Address
www.zelquin.com

It should use simple iconography for each one of those fields.

Font styles to use
Other font styles liked:
• Co, Jubilat, Avenir

Colors

Designer to choose colors to be used in the design.

Requirements
Must have
• Clean aesthetic,
• Good use of negative space.
• It should use our company logo, shown in the attached file. It is able to use the negative of that logo (coloured font and white background) and I have attached other acceptable accent colours in a swatch file.
Should not have
• Should not be too busy
• No extraneous text (slogans, tag lines etc)

```html
<!DOCTYPE html>
<html lang="en">
<head>
<meta charset="utf-8">
<title>Zelquin Business Card</title>
<link rel="stylesheet" href="https://fonts.googleapis.com/css2?family=Open+Sans:wght@400;600&display=swap">
<style>
  :root {
    --backdrop: #3b3b3d;
    --card: #1e1e20;
    --card-edge: #2a2a2c;
    --emboss: #121213;
    --teal: #45b6b9;
    --white: #ffffff;
    --text-light: #e4e4e4;
    --text-muted: #cfcfcf;
  }
  * { margin: 0; padding: 0; box-sizing: border-box; }
  html, body {
    width: 799px;
    height: 1200px;
    overflow: hidden;
    background: var(--backdrop);
    font-family: "Open Sans", sans-serif;
  }
  .sheet {
    position: relative;
    width: 799px;
    height: 1200px;
  }
  .card {
    position: absolute;
    left: 90px;
    width: 620px;
    height: 354px;
    border-radius: 26px;
    background: var(--card);
    border: 1px solid var(--card-edge);
    overflow: hidden;
  }
  .card--front { top: 123px; }
  .card--back  { top: 723px; }

  /* Front */
  .front-wordmark {
    position: absolute;
    inset: 0;
    display: flex;
    align-items: center;
    justify-content: center;
    font-weight: 600;
    font-size: 70px;
    letter-spacing: 3px;
    color: var(--emboss);
  }

  /* Back */
  .brand-band {
    position: absolute;
    left: 0;
    right: 0;
    top: 68px;
    height: 104px;
    background: var(--teal);
  }
  .brand-band__name {
    position: absolute;
    right: 62px;
    top: 50%;
    transform: translateY(-50%);
    font-weight: 600;
    font-size: 64px;
    letter-spacing: 3px;
    color: var(--white);
    line-height: 1;
  }
  .rule {
    position: absolute;
    left: 0;
    height: 1px;
    background: var(--teal);
  }
  .rule--top { top: 190px; width: 560px; }
  .rule--bottom { top: 318px; left: 40px; width: 540px; }

  .identity {
    position: absolute;
    top: 204px;
    left: 0;
    right: 0;
    text-align: center;
  }
  .identity__name {
    font-weight: 600;
    font-size: 21px;
    color: var(--text-light);
    line-height: 1.2;
  }
  .identity__title {
    font-size: 14px;
    color: var(--teal);
    margin-top: 2px;
  }

  .contacts {
    position: absolute;
    top: 274px;
    left: 0;
    right: 0;
    display: flex;
    justify-content: center;
    gap: 26px;
    list-style: none;
  }
  .contacts__item {
    display: flex;
    align-items: center;
    gap: 8px;
    font-size: 14px;
    color: var(--text-muted);
    white-space: nowrap;
  }
  .contacts__icon {
    width: 18px;
    height: 18px;
    flex: none;
  }
</style>
</head>
<body>
<main class="sheet">
  <section class="card card--front" aria-label="Card front">
    <div class="front-wordmark">ZELQUIN</div>
  </section>

  <section class="card card--back" aria-label="Card back">
    <div class="brand-band">
      <span class="brand-band__name">ZELQUIN</span>
    </div>
    <div class="rule rule--top"></div>

    <div class="identity">
      <p class="identity__name">Jane Roe Miller</p>
      <p class="identity__title">Managing Director</p>
    </div>

    <ul class="contacts">
      <li class="contacts__item">
        <svg class="contacts__icon" viewBox="0 0 18 18" aria-hidden="true">
          <circle cx="9" cy="9" r="8" fill="none" stroke="var(--teal)" stroke-width="1.4"/>
          <path d="M6.2 5.2l1.5 1.6-.8 1.1c.5 1 1.2 1.7 2.2 2.2l1.1-.8 1.6 1.5-.9 1.3c-2.9-.4-5.1-2.6-5.5-5.5z" fill="var(--teal)"/>
        </svg>
        415.555.0182
      </li>
      <li class="contacts__item">
        <svg class="contacts__icon" viewBox="0 0 18 18" aria-hidden="true">
          <circle cx="9" cy="9" r="8" fill="none" stroke="var(--teal)" stroke-width="1.4"/>
          <rect x="5" y="6.2" width="8" height="5.6" fill="var(--teal)"/>
          <path d="M5 6.4l4 3 4-3" fill="none" stroke="var(--card)" stroke-width="0.9"/>
        </svg>
        janeroe@zelquin.com
      </li>
      <li class="contacts__item">
        <svg class="contacts__icon" viewBox="0 0 18 18" aria-hidden="true">
          <circle cx="9" cy="9" r="8" fill="none" stroke="var(--teal)" stroke-width="1.4"/>
          <circle cx="9" cy="9" r="4.2" fill="none" stroke="var(--teal)" stroke-width="1"/>
          <ellipse cx="9" cy="9" rx="1.8" ry="4.2" fill="none" stroke="var(--teal)" stroke-width="0.9"/>
          <path d="M4.8 9h8.4" stroke="var(--teal)" stroke-width="0.9"/>
        </svg>
        www.zelquin.com
      </li>
    </ul>

    <div class="rule rule--bottom"></div>
  </section>
</main>
</body>
</html>
```